Machinery Harbor Corp - Business Card Design

Need a new modern designed business card that is different and stands out to represent my equipment financing company. Machinery Harbor Corp finances all types of equipment and all types of industries. We like to do equipment financing a different way by putting customers first and want our card to represent that different approach to business. I want a card that some remembers when they receive it so it sticks in their mind and makes that wow impression.

Card should have a black background so the logo stands out. It can be horizontial or vertical or a combination of both.

Front of card information is below that shows the information that would go on my card. That is where I want a different look or design to stand out. The front could be split black/orange colour so the logo could pop on black side and information on orange side with different lettering. Just outside the box thinking on the front of the card. Open to any type of design.

Back of card is below which i I like unless you have a different spin to provide or a different idea that would make the card better as I am open to anything that looks great.

Target Market(s)

Machinery Harbor Corp deals with business owners in all industries.

Industry/Entity Type

Business

Contact Information for Business Card

Colors

Designer to choose colors to be used in the design.

Requirements
Must have
• Modern
• Different
• Stand Out
• Makes an Impression

```html
<!DOCTYPE html>
<html lang="en">
<head>
<meta charset="utf-8">
<title>Machinery Harbor Corp – Business Card</title>
<link href="https://fonts.googleapis.com/css2?family=Lato:wght@400;700;900&display=swap" rel="stylesheet">
<style>
  :root {
    --stage: #2b2623;
    --card: #050505;
    --orange: #ff8a1f;
    --orange-deep: #ff5a1a;
    --text: #ffffff;
    --ink: #141414;
  }
  * { box-sizing: border-box; margin: 0; padding: 0; }
  html, body { width: 1200px; height: 780px; overflow: hidden; }
  body {
    background: var(--stage);
    font-family: "Lato", Arial, sans-serif;
    color: var(--text);
    position: relative;
  }
  .card {
    position: absolute;
    top: 235px;
    width: 540px;
    height: 309px;
    background: var(--card);
    overflow: hidden;
    box-shadow: 0 14px 30px rgba(0,0,0,.45);
  }
  .card--back { left: 30px; }
  .card--front { left: 630px; }

  .band {
    position: absolute;
    left: 0; right: 0;
    height: 10px;
    background: linear-gradient(90deg, var(--orange-deep), var(--orange));
  }
  .band--top { top: 0; }
  .band--bottom { bottom: 0; }

  .mark-dot {
    flex: none;
    width: 18px; height: 18px; border-radius: 50%;
    background: var(--orange);
  }
  .wordmark {
    font-weight: 700;
    color: var(--orange);
    letter-spacing: .06em;
    text-transform: uppercase;
    white-space: nowrap;
  }

  /* back */
  .back-mark {
    position: absolute;
    left: 0; right: 0; top: 112px;
    display: flex; align-items: center; justify-content: center; gap: 12px;
  }
  .back-mark .wordmark { font-size: 24px; }
  .back-url {
    position: absolute;
    left: 0; right: 0; top: 186px;
    text-align: center;
    font-size: 14px;
  }

  /* front */
  .front-mark {
    position: absolute;
    left: 60px; top: 56px;
    display: flex; align-items: center; gap: 12px;
  }
  .front-mark .mark-dot { width: 16px; height: 16px; }
  .front-mark .wordmark { font-size: 20px; line-height: 1.15; }
  .wordmark__line { display: block; }

  .name-tab {
    position: absolute;
    right: 0; top: 62px;
    width: 210px; height: 62px;
    border-radius: 31px 0 0 31px;
    background: linear-gradient(90deg, var(--orange-deep), var(--orange));
    color: var(--ink);
    padding: 12px 0 0 40px;
  }
  .name-tab__name { font-size: 18px; font-weight: 900; letter-spacing: .03em; line-height: 1.1; white-space: nowrap; }
  .name-tab__title { font-size: 13px; font-weight: 700; letter-spacing: .06em; }

  .rule {
    position: absolute;
    height: 3px;
    background: var(--orange-deep);
  }
  .rule--main { left: 0; right: 0; top: 204px; }
  .rule--phone { left: 290px; right: 20px; top: 150px; }

  .icon-dot {
    position: absolute;
    width: 28px; height: 28px; border-radius: 50%;
    background: var(--orange-deep);
    display: flex; align-items: center; justify-content: center;
  }
  .icon-dot svg { width: 16px; height: 16px; }
  .icon-dot--mail { left: 120px; top: 192px; }
  .icon-dot--phone { left: 405px; top: 138px; }
  .icon-dot--web { left: 390px; top: 192px; }

  .contact { position: absolute; font-size: 14px; white-space: nowrap; }
  .contact--mail { left: 32px; top: 232px; }
  .contact--phone { left: 372px; top: 174px; font-size: 15px; }
  .contact--web { left: 282px; top: 232px; }
</style>
</head>
<body>

<section class="card card--back" aria-label="Card back">
  <div class="band band--top"></div>
  <div class="back-mark">
    <span class="mark-dot"></span>
    <span class="wordmark">Machinery Harbor Corp</span>
  </div>
  <p class="back-url">www.machineryharborcorp.ca</p>
  <div class="band band--bottom"></div>
</section>

<section class="card card--front" aria-label="Card front">
  <div class="front-mark">
    <span class="mark-dot"></span>
    <span class="wordmark">
      <span class="wordmark__line">Machinery</span>
      <span class="wordmark__line">Harbor Corp</span>
    </span>
  </div>

  <div class="name-tab">
    <p class="name-tab__name">DEAN MARLOW</p>
    <p class="name-tab__title">PRESIDENT</p>
  </div>

  <div class="rule rule--phone"></div>
  <div class="icon-dot icon-dot--phone">
    <svg viewBox="0 0 16 16" aria-hidden="true"><path fill="#141414" d="M3 2h3l1 3-2 1.2a8 8 0 0 0 4.8 4.8L11 9l3 1v3c0 .6-.4 1-1 1A12 12 0 0 1 2 3c0-.6.4-1 1-1z"/></svg>
  </div>
  <p class="contact contact--phone">403.555.0192</p>

  <div class="rule rule--main"></div>
  <div class="icon-dot icon-dot--mail">
    <svg viewBox="0 0 16 16" aria-hidden="true"><rect x="2" y="4" width="12" height="8" fill="none" stroke="#141414" stroke-width="1.5"/><path d="M2 4l6 5 6-5" fill="none" stroke="#141414" stroke-width="1.5"/></svg>
  </div>
  <div class="icon-dot icon-dot--web">
    <svg viewBox="0 0 16 16" aria-hidden="true"><g fill="none" stroke="#141414" stroke-width="1.3"><circle cx="8" cy="8" r="6"/><ellipse cx="8" cy="8" rx="2.6" ry="6"/><path d="M2 8h12M3 5h10M3 11h10"/></g></svg>
  </div>
  <p class="contact contact--mail">dean@machineryharborcorp.ca</p>
  <p class="contact contact--web">www.machineryharborcorp.ca</p>

  <div class="band band--bottom"></div>
</section>

</body>
</html>
```